Salmon Shop that sells both wholesale and retail salmon in a variety of ways.

"Reef Harvest" is a business that is selling atlantic salmon in every way possible. We will be a salmon butcher to the public for retail purchase and we will also be out and about trying to sell our products to restaurants cafes and any other wholesale way. Our product is from Tasmania but we will be trading on the Sunshine Coast. The shop design has an urban, rustic feel and very much about the product. One of the owners has worked on salmon farms for 15 years and we want it to be very specialised and quality. I have nothing to offer you to help with this design....I would like both a salmon on the card, not sure if image or silohette is best and would like the other side to have a fillet with a tag of some sort. We are looking for a logo also. Use a photo of an Atlantic Salmon, Atlantic Salmon have two fins along the back.
Updates

Project Deadline Extended Reason: I am extending the deadline as I have still not got exactly what I want. All designers have added something great to what I am after and I just need someone to pull it all together. I have put in a new brief with a sketched image to help so we can get this perfect. Please read all the instructions. Thank you Added Monday, February 16, 2015

Target Market(s)

Restaurants, cafes

Industry/Entity Type

Retail

Contact Information for Business Card

Reef Harvest (Not to have "Shop" at the end.Shop 12/130-164 Brisbane RdMooloolaba 4557

Colors
1c66ab

Requirements
Must have
• logo for reef harvest with the S being salmon fillet of fresh salmon on white platemap of tasmaniasepia /black and white image of atlantic salmon
Nice to have
• fillet of salmonmap of tasmaniasalmon
Should not have
• Not Shop at the end.

```html
<!DOCTYPE html>
<html lang="en">
<head>
<meta charset="utf-8">
<title>Reef Harvest – Business Card</title>
<link rel="stylesheet" href="https://fonts.googleapis.com/css2?family=Open+Sans:wght@300;400&family=Varela+Round&display=swap">
<style>
  :root {
    --bg: #e4e6f0;
    --wood-light: #c58a4e;
    --wood-mid: #a8693a;
    --wood-dark: #7a4a26;
    --brand-teal: #2aa3c6;
    --panel-grey: #e9e9ea;
    --panel-grey-dark: #d6d6d8;
    --ink: #3a3a3a;
    --white: #ffffff;
    --plate-rim: #f4f4f4;
    --salmon: #e8875c;
    --lemon: #f3d75a;
    --greens: #5a8f3a;
  }
  * { box-sizing: border-box; margin: 0; padding: 0; }
  html, body { width: 1200px; height: 800px; overflow: hidden; }
  body {
    background: var(--bg);
    font-family: "Open Sans", Arial, sans-serif;
    position: relative;
  }
  .card {
    position: absolute;
    top: 240px;
    width: 560px;
    height: 320px;
    overflow: hidden;
    box-shadow: 0 6px 16px rgba(0,0,0,0.18);
  }
  .card--front { left: 30px; }
  .card--back { left: 610px; }

  .wood {
    position: absolute;
    background: linear-gradient(172deg, var(--wood-light) 0%, var(--wood-mid) 45%, var(--wood-light) 70%, var(--wood-dark) 100%);
  }
  .card--front .wood { inset: 0; }

  .front-wordmark {
    position: absolute;
    top: 26px;
    right: 210px;
    font-family: "Varela Round", Arial, sans-serif;
    font-size: 44px;
    color: rgba(255,255,255,0.35);
    letter-spacing: 1px;
  }
  .contact {
    position: absolute;
    top: 100px;
    left: 34px;
    color: var(--white);
    font-weight: 300;
  }
  .contact__name { font-size: 24px; margin-bottom: 6px; letter-spacing: 0.5px; }
  .contact__line {
    display: flex; align-items: center; gap: 8px;
    font-size: 15px; line-height: 22px;
  }
  .contact__line svg { width: 12px; height: 12px; flex: none; }
  .contact__indent { padding-left: 20px; font-size: 15px; line-height: 22px; }

  .plate {
    position: absolute;
    right: -20px;
    bottom: -20px;
    width: 300px;
    height: 330px;
    border-radius: 70% 0 0 0 / 55% 0 0 0;
    background: var(--plate-rim);
    padding: 10px 0 0 10px;
    box-shadow: -2px -2px 8px rgba(0,0,0,0.25);
  }
  .plate__photo {
    width: 100%; height: 100%;
    border-radius: 70% 0 0 0 / 55% 0 0 0;
    background: radial-gradient(circle at 35% 45%, var(--lemon) 0%, var(--salmon) 30%, var(--greens) 70%, var(--salmon) 100%);
  }

  .card--back .wood { top: 0; left: 0; right: 0; height: 190px; }
  .back-wordmark {
    position: absolute;
    top: 62px; left: 0; right: 0;
    text-align: center;
    font-family: "Varela Round", Arial, sans-serif;
    font-size: 62px;
    color: var(--brand-teal);
  }
  .divider {
    position: absolute;
    top: 190px; left: 0; right: 0;
    height: 6px;
    background: var(--brand-teal);
  }
  .grey-panel {
    position: absolute;
    top: 196px; left: 0; right: 0; bottom: 0;
    background: linear-gradient(180deg, var(--panel-grey) 0%, var(--panel-grey-dark) 100%);
  }
  .fish-photo {
    position: absolute;
    top: 14px; left: 150px;
    width: 250px; height: 60px;
    border-radius: 50%;
    background: linear-gradient(180deg, #8a8f93 0%, #d8dadc 55%, #f2f2f2 100%);
  }
  .website {
    position: absolute;
    bottom: 16px; left: 0; right: 0;
    text-align: center;
    font-size: 21px;
    color: var(--ink);
  }
</style>
</head>
<body>
  <section class="card card--front" aria-label="Business card front">
    <div class="wood" role="img" aria-label="Rustic wooden plank background"></div>
    <div class="front-wordmark">Reef Harvest</div>
    <div class="contact">
      <p class="contact__name">Liam Carter</p>
      <p class="contact__line">
        <svg viewBox="0 0 12 12"><rect x="2" y="0.5" width="8" height="11" rx="1.5" fill="none" stroke="#fff" stroke-width="1.2"/><circle cx="6" cy="9.5" r="0.8" fill="#fff"/></svg>
        0000-000-000
      </p>
      <p class="contact__line">
        <svg viewBox="0 0 12 12"><rect x="0.6" y="2" width="10.8" height="8" fill="none" stroke="#fff" stroke-width="1.2"/><path d="M0.6 2 L6 6.5 L11.4 2" fill="none" stroke="#fff" stroke-width="1.2"/></svg>
        hello@reefharvest.com.au
      </p>
      <p class="contact__line">
        <svg viewBox="0 0 12 12"><path d="M6 11.5 C3 8 2 6 2 4.5 A4 4 0 0 1 10 4.5 C10 6 9 8 6 11.5Z" fill="#fff"/><circle cx="6" cy="4.5" r="1.4" fill="#a8693a"/></svg>
        Shop 7/212-238 Kellaway Rd.
      </p>
      <p class="contact__indent">Kellaway Bay 4571</p>
    </div>
    <div class="plate">
      <div class="plate__photo" role="img" aria-label="Grilled salmon fillets with lemon slices and green beans on a white plate"></div>
    </div>
  </section>

  <section class="card card--back" aria-label="Business card back">
    <div class="wood" role="img" aria-label="Rustic wooden plank background"></div>
    <div class="back-wordmark">Reef Harvest</div>
    <div class="divider"></div>
    <div class="grey-panel">
      <div class="fish-photo" role="img" aria-label="Photo of a whole Atlantic salmon"></div>
      <p class="website">www.reefharvest.com.au</p>
    </div>
  </section>
</body>
</html>
```